Bold, Modern, Clean "Kestrelwaymassage.com" website

Why we stand out?
We are a male and female mobile massage team. Our names are Paul and Lina. 
Kestrel Way is a Seattle based mobile massage service. Our massage is offered to the community with a goal of facilitating balance within each individual. We specialize in integrated Pain management, and sports/medical massage therapy. Every client's first assessment is attended by our male and female massage therapist team. Depending on the goals identified for an individual determines which therapist will be assigned to provide treatment, if not both.

Our passion...
Here at Kestrel Way, we have a great passion for Postural Resoration and how it is integrated into an individual's Massage treatment. We pride ourselves in being natural facilitators of healing, which takes the ego of the therapist out of the client's healing process. We strive to deliver the best massage possible by including modalities such as Neuromuscular, Myofascial release, spontaneous muscle release, postural restoration, orthopedic, and medical massage.

Our education...

We are both Graduates of Venmora, school of massage therapy. We have continuing education in medical massage, myofacial release, trigger point therapy, postural restoration, anatomy, and spontaneous muscle release. Lina is also a Certified Yoga Instructor, which amplifies her experience with flexibility and strength as it pertains to each individual. Paul's passion is Massage, stretching, and strength training to encourage postural restoration and realignment.

Our rates-

Our rates are $75/ 60 minutes, $95/ 90 minutes, and $120/ 120 minutes.

Education-
Both Lina and I worked as behavioral health professionals that specialized in life skills mentoring for youth who had experienced different types of trauma. This led us both to want to help others in a different environment, where individuals can be empowered to take responsibility over their own healing. To us, massage is a type of manipulation physical therapy, that encourages healing on many levels.

Advice to any massage client-
The most important thing to 'us', as Licenced providers is to get you on to our table to show you our skills. But a good therapist never forgets that it's not about what we do for you, but what we can facilitate for you. Your health and healing has nothing to do with us. It is yours, not ours. Identify what your goals are with any Therapist, and know what the end looks like. Progress should be tangible, such as range of motion, and decreased pain.

Lina and Paul at Kestrel Way are awesome! I recently had open heart surgery, and Lina worked on me to increase my range of motion while helping with the pinched nerve from my arm being in the same position for so long during my surgery. My wife drives a lot for work, and Paul has helped decrease her neck and lower back pain immensely. They are seriously the best therapists I have ever worked with. I would recommend them to anyone who needs anything from stress relief to a medical massage treatment. They are professional, up beat, easy going, and always on time. And, I love that they meet us where ever we like! We did a staycation recently, where they came to our hotel to give us relaxation massages. Although usually they come to our home, where we focus on pain related issues. We will continue to work with them for a long, long time.

Target Market(s)

Mobile massage therapy clients

Industry/Entity Type

Massage Therapy

Coding

Coded - Design and coding required

Number of Pages Required

1 page

Font styles to use
Serif
Sans Serif

Requirements
Must have
• Please add or remove any information that would help the presentation of our website. Our logo is posted below, please include into the website.
• Please include a contact field that includes, kestrelwaymassage@fernmail.net,
• (206) 555-0148
• We have also included our own stock photos, as well as a photo of Paul and Lina. Please include a cropped photo of both massage therapists.

```html
<!DOCTYPE html>
<html lang="en">
<head>
<meta charset="utf-8">
<title>Kestrel Way – Mobile Massage</title>
<link href="https://fonts.googleapis.com/css2?family=Dancing+Script:wght@700&family=Montserrat:wght@500&family=Open+Sans:wght@400;600&family=Roboto:wght@400;500;700&display=swap" rel="stylesheet">
<style>
:root{
  --teal:#19c2b3;
  --navy:#1a2fb8;
  --logo-blue:#1638c8;
  --ink:#1b1b1b;
  --black:#000;
  --white:#fff;
  --strip:#efefef;
  --about-a:#3a2418;
  --about-b:#6b4a36;
  --edu-a:#2e2e2e;
  --edu-b:#575757;
  --touch-a:#e9e4dc;
  --touch-b:#f7f4ef;
}
*{box-sizing:border-box;margin:0;padding:0}
html,body{width:1200px;height:3704px;overflow:hidden}
body{position:relative;background:var(--white);font-family:"Roboto",Arial,sans-serif;color:var(--ink)}
.abs{position:absolute}
.script{font-family:"Dancing Script",cursive;font-weight:700}

/* top bar */
.topbar{left:0;top:0;width:1200px;height:49px;background:var(--black)}
.topbar .soc{position:absolute;top:18px;width:13px;height:13px;border-radius:50%;border:2px solid var(--white)}

/* navigation */
.nav{left:0;top:49px;width:1200px;height:136px;background:var(--white)}
.nav a{position:absolute;top:60px;font-size:15px;color:var(--ink);text-decoration:none;transform:translateX(-50%)}
.nav a.active{color:var(--teal)}
.nav .active-bar{position:absolute;left:128px;top:0;width:99px;height:6px;background:var(--teal)}
.logo{display:flex;align-items:center;justify-content:center;border-radius:50%;background:var(--logo-blue);color:var(--white);font-family:"Roboto",sans-serif;font-weight:700;text-align:center;line-height:1.05}
.nav .logo{position:absolute;left:538px;top:7px;width:124px;height:124px;font-size:22px}

/* hero */
.hero{left:0;top:188px;width:1200px;height:470px;
  background:
    linear-gradient(180deg,rgba(60,40,20,.55) 0%,rgba(60,40,20,0) 45%,rgba(255,255,255,0) 72%,rgba(250,246,240,.9) 88%,#f6f1ea 100%),
    linear-gradient(100deg,#6e5434 0%,#a47b52 18%,#d8ad86 34%,#e9c3a0 46%,#cfa27c 56%,#f2ebe2 68%,#faf7f2 82%,#efe2d6 100%);}
.hero .arrow{position:absolute;top:225px}
.hero .dots{position:absolute;left:0;top:427px;width:1200px;display:flex;justify-content:center;gap:12px;align-items:center}
.hero .dots span{width:10px;height:10px;border-radius:50%;background:#222}
.hero .dots span.on{width:16px;height:16px;background:transparent;border:2px solid #222}
.hero .dots .line{position:absolute;top:7px;height:2px;background:#333;width:250px}

/* section titles */
.title{left:0;width:1200px;display:flex;justify-content:center;align-items:center;gap:30px;color:var(--teal);font-size:64px}
.title::before,.title::after{content:"";width:100px;height:2px;background:var(--teal)}
.title.light{color:var(--white)}
.title.light::before,.title.light::after{background:var(--white)}

/* services */
.card{width:457px;height:192px;border:2px solid #7fd8cf;overflow:hidden;background:var(--white)}
.card .photo{position:absolute;left:0;top:0;width:270px;height:100%;background:linear-gradient(90deg,#8a8a86,#cfcac2 50%,rgba(255,255,255,0))}
.card h3{position:absolute;left:146px;top:36px;font-size:18px;font-weight:400;white-space:nowrap;letter-spacing:.2px}
.card p{position:absolute;left:146px;top:80px;width:290px;font-size:13.5px;line-height:23px;color:var(--ink)}

/* about */
.about{left:0;top:1264px;width:1200px;height:415px;background:linear-gradient(90deg,var(--about-a),var(--about-b) 60%,#8a6a52)}
.about p{position:absolute;left:79px;top:176px;width:640px;font-size:15.5px;line-height:28px;color:var(--white)}
.polaroid{background:var(--white);padding:14px 14px 40px;box-shadow:0 4px 14px rgba(0,0,0,.45)}
.polaroid div{width:100%;height:100%}

/* rates */
.rate{width:188px;height:188px}
.rate .label{position:absolute;left:0;top:0;width:188px;height:188px;display:flex;flex-direction:column;align-items:center;justify-content:center;font-family:"Montserrat",sans-serif;font-weight:500;font-size:22px;line-height:28px;color:var(--ink)}

/* education */
.edu{left:0;top:2066px;width:1200px;height:415px;background:linear-gradient(100deg,var(--edu-a),var(--edu-b) 65%,#3d3d3d)}
.edu p{position:absolute;left:140px;top:146px;width:920px;text-align:center;font-size:14.5px;line-height:27px;color:var(--white)}
.btn{display:flex;align-items:center;justify-content:center;font-family:"Roboto",sans-serif;font-weight:700;font-size:17px;letter-spacing:.5px}
.edu .btn{position:absolute;left:506px;top:284px;width:185px;height:62px;border:2px solid var(--white);color:var(--white)}

/* testimonial */
.quote-mark{left:0;top:2612px;width:1200px;text-align:center;font-family:Georgia,serif;font-size:60px;font-weight:700;line-height:1}
.testimonial{left:140px;top:2656px;width:920px;text-align:center;font-size:14.5px;line-height:27px;color:var(--ink)}
.author{left:0;top:2744px;width:1200px;text-align:center;font-size:18px;font-weight:700}
.tdots{left:0;top:2805px;width:1200px;display:flex;justify-content:center;gap:10px}
.tdots span{width:12px;height:12px;background:var(--black)}
.tdots span.on{background:var(--white);border:2px solid var(--black)}

/* contact form */
.touch{left:0;top:2869px;width:1200px;height:415px;background:linear-gradient(90deg,#d9cfc4,var(--touch-b) 30%,var(--touch-a) 70%,#d6c9bb)}
.field{border-bottom:1.5px solid #333;font-size:14px;color:var(--ink);padding-bottom:8px}
.touch .btn{position:absolute;left:506px;top:284px;width:185px;height:62px;border:2px solid #333;color:var(--ink);background:rgba(255,255,255,.5)}

/* contact strip */
.strip{left:0;top:3284px;width:1200px;height:104px;background:var(--strip)}
.strip .item{position:absolute;top:38px;display:flex;align-items:center;gap:22px;font-family:"Open Sans",sans-serif;font-size:21px;color:var(--ink)}

/* footer */
.footer{left:0;top:3388px;width:1200px;height:316px;background:var(--black)}
.footer .logo{position:absolute;left:551px;top:52px;width:98px;height:98px;font-size:17px}
.footer .soc{position:absolute;top:180px;width:54px;height:54px;border-radius:50%;border:2px solid var(--white)}
.footer .copy{position:absolute;left:0;top:254px;width:1200px;text-align:center;font-size:13px;color:var(--teal)}
</style>
</head>
<body>

<header>
  <div class="abs topbar">
    <span class="soc" style="left:530px"></span>
    <span class="soc" style="left:564px"></span>
    <span class="soc" style="left:598px"></span>
    <span class="soc" style="left:632px"></span>
  </div>
  <nav class="abs nav">
    <span class="active-bar"></span>
    <a class="active" href="#" style="left:173px">Home</a>
    <a href="#" style="left:301px">About us</a>
    <a href="#" style="left:437px">Our Rate</a>
    <div class="logo">Kestrel<br>Way</div>
    <a href="#" style="left:768px">Education</a>
    <a href="#" style="left:896px">Testimonial</a>
    <a href="#" style="left:1037px">Contact Us</a>
  </nav>
</header>

<section class="abs hero" role="img" aria-label="Therapist giving a back massage to a relaxed client lying on a white towel with scattered rose petals">
  <svg class="arrow" style="left:14px" width="44" height="44" viewBox="0 0 44 44" fill="none" stroke="#fff" stroke-width="2.5"><rect x="2" y="2" width="40" height="40"/><path d="M32 22H12M20 14l-8 8 8 8"/></svg>
  <svg class="arrow" style="left:1138px" width="50" height="44" viewBox="0 0 50 44" fill="none" stroke="#fff" stroke-width="2.5"><path d="M10 2h30v12M40 30v12H10"/><path d="M4 22h30M26 14l8 8-8 8"/></svg>
  <div class="dots">
    <span class="line" style="left:310px"></span>
    <span></span><span class="on"></span><span></span><span></span>
    <span class="line" style="left:640px"></span>
  </div>
</section>

<main>
  <h2 class="abs title script" style="top:700px">Services</h2>

  <article class="abs card" style="left:136px;top:802px">
    <div class="photo" role="img" aria-label="Therapist guiding a neuromuscular stretch"></div>
    <h3>NEUROMUSCULAR</h3>
    <p>Lorem ipsum dolor sit amet, consectetur adipisicing elit, sed do eiusmod tempor incididunt ut labore et dolore magna aliqua.</p>
  </article>
  <article class="abs card" style="left:605px;top:802px">
    <div class="photo" role="img" aria-label="Therapist assisting a muscle release stretch"></div>
    <h3>SPONTANEOUS MUSCLE RELEASE</h3>
    <p>Lorem ipsum dolor sit amet, consectetur adipisicing elit, sed do eiusmod tempor incididunt ut labore et dolore magna aliqua.</p>
  </article>
  <article class="abs card" style="left:136px;top:1005px">
    <div class="photo" role="img" aria-label="Postural restoration leg treatment"></div>
    <h3>POSTURAL RESTORATION</h3>
    <p>Lorem ipsum dolor sit amet, consectetur adipisicing elit, sed do eiusmod tempor incididunt ut labore et dolore magna aliqua.</p>
  </article>
  <article class="abs card" style="left:605px;top:1005px">
    <div class="photo" style="background:linear-gradient(90deg,#4e7a6a,#a6bfb5 50%,rgba(255,255,255,0))" role="img" aria-label="Medical massage on a client's shoulder"></div>
    <h3>MEDICAL MASSAGE</h3>
    <p>Lorem ipsum dolor sit amet, consectetur adipisicing elit, sed do eiusmod tempor incididunt ut labore et dolore magna aliqua.</p>
  </article>

  <section class="abs about" role="img" aria-label="Warm toned massage room background">
    <h2 class="abs title light script" style="left:-165px;top:80px;font-size:62px">Know About Us</h2>
    <p>We are a male and female mobile massage team. Our names are Paul and Lina. Kestrel Way is a Seattle based mobile massage service. Our massage is offered to the community with a goal of facilitating balance within each individual. We specialize in integrated Pain management, and sports/medical massage therapy. Every client's first assessment is attended by our male and female massage therapist team.</p>
    <div class="abs polaroid" style="left:738px;top:28px;width:232px;height:250px;transform:rotate(-6deg)">
      <div role="img" aria-label="Photo of Paul" style="background:linear-gradient(135deg,#8fa3b5,#5b6e7e)"></div>
    </div>
    <div class="abs polaroid" style="left:880px;top:135px;width:252px;height:250px;transform:rotate(6deg)">
      <div role="img" aria-label="Photo of Lina" style="background:linear-gradient(135deg,#9a8a80,#5a4c44)"></div>
    </div>
  </section>

  <h2 class="abs title script" style="top:1718px">Our Rate</h2>

  <div class="abs rate" style="left:296px;top:1838px">
    <svg width="188" height="188" viewBox="0 0 188 188" fill="none"><circle cx="94" cy="94" r="84" stroke="var(--navy)" stroke-width="5"/><path d="M22 76A74 74 0 0 1 104 21" stroke="var(--teal)" stroke-width="5"/></svg>
    <div class="label"><span>$ 75 / 60</span><span>Minutes</span></div>
  </div>
  <div class="abs rate" style="left:506px;top:1838px">
    <svg width="188" height="188" viewBox="0 0 188 188" fill="none"><circle cx="94" cy="94" r="84" stroke="var(--navy)" stroke-width="5"/><path d="M22 76A74 74 0 0 1 104 21" stroke="var(--teal)" stroke-width="5"/></svg>
    <div class="label"><span>$ 95 / 90</span><span>Minutes</span></div>
  </div>
  <div class="abs rate" style="left:716px;top:1838px">
    <svg width="188" height="188" viewBox="0 0 188 188" fill="none"><circle cx="94" cy="94" r="84" stroke="var(--navy)" stroke-width="5"/><path d="M22 76A74 74 0 0 1 104 21" stroke="var(--teal)" stroke-width="5"/></svg>
    <div class="label"><span>$ 120 / 120</span><span>Minutes</span></div>
  </div>

  <section class="abs edu" role="img" aria-label="Dim studio wall with plants in the background">
    <h2 class="abs title light script" style="top:46px;font-size:62px">Our Education</h2>
    <p>We are both Graduates of Venmora, school of massage therapy. We have continuing education in medical massage, myofacial release, trigger point therapy, postural restoration, anatomy, and spontaneous muscle release. Lina is also a Certified Yoga Instructor, which amplifies her experience with flexibility and strength as it pertains to each individual. Paul's passion is Massage, stretching, and strength training to encourage postural restoration and realignment</p>
    <a class="btn">READ MORE</a>
  </section>

  <h2 class="abs title script" style="top:2506px">Testimonial</h2>
  <div class="abs quote-mark">&ldquo;</div>
  <p class="abs testimonial">Lina and Paul at Kestrel Way are awesome! I recently had open heart surgery, and Lina worked on me to increase my range of motion while helping with the pinched nerve from my arm being in the same position for so long during my surgery. My wife drives a lot for work, and Paul has helped decrease her neck and lower back pain immensely. They are seriously the best therapists I have ever worked with</p>
  <div class="abs author">- Darcy T.</div>
  <div class="abs tdots"><span></span><span class="on"></span><span></span><span></span><span></span><span></span></div>

  <section class="abs touch" role="img" aria-label="Couple relaxing during side by side massages">
    <h2 class="abs title script" style="top:32px;font-size:62px">Keep In Touch</h2>
    <div class="abs field" style="left:264px;top:148px;width:341px">Name</div>
    <div class="abs field" style="left:635px;top:148px;width:353px">Email Id</div>
    <div class="abs field" style="left:264px;top:192px;width:724px;height:70px">Message</div>
    <a class="btn">SUBMIT</a>
  </section>
</main>

<section class="abs strip">
  <div class="item" style="left:252px">
    <svg width="24" height="24" viewBox="0 0 24 24" fill="var(--teal)"><path d="M6.6 10.8a15.1 15.1 0 0 0 6.6 6.6l2.2-2.2a1 1 0 0 1 1-.25 11.4 11.4 0 0 0 3.6.57 1 1 0 0 1 1 1V20a1 1 0 0 1-1 1A17 17 0 0 1 3 4a1 1 0 0 1 1-1h3.5a1 1 0 0 1 1 1c0 1.25.2 2.45.57 3.57a1 1 0 0 1-.25 1z"/></svg>
    <span>(206) 555-0148</span>
  </div>
  <div class="item" style="left:594px">
    <svg width="22" height="18" viewBox="0 0 22 18" fill="var(--teal)"><path d="M0 0h22v3l-11 7L0 3z"/><path d="M0 5l11 7 11-7v13H0z"/></svg>
    <span>kestrelwaymassage@fernmail.net</span>
  </div>
</section>

<footer class="abs footer">
  <div class="logo">Kestrel<br>Way</div>
  <span class="soc" style="left:467px"></span>
  <span class="soc" style="left:538px"></span>
  <span class="soc" style="left:610px"></span>
  <span class="soc" style="left:682px"></span>
  <p class="copy">© Kestrel Way mobile massage - 2015. All rights reserved.</p>
</footer>

</body>
</html>
```